Glen Whitmore Professional Coaching

I would like a website with a mountain theme geared towards professional executives reaching higher peaks and goals. This is a 3 page website with brand essence information on the opening page, the coaching process on a second page and "about me" and lead capture form on a third page

Target Market(s)

C-Level audience, involved in tech, government, manufacturing, and transportation type of corporations

Coding

Coded - Design and coding required

Number of Pages Required

3 page

Font styles to use
Sans Serif

Colors
a7a7a7
1b1b1b
e8e8e8
3176b5
abd036
0355a3

Requirements
Must have
• Looking for a user friendly site that I can manage/update going forward. Must have:
• 1. "Is coaching right for you?" - page 1
• 2. "Our Process" page 2 - I will describe how we approach coaching
• 3. "Contact us" page 3 where I can capture contact information from potential clients
• 4. Clean and professional with more modern font
• 5. Links to personal social media sites
• 6. Ability to upload/download .pdf documents as resources
• 7. Ability to add on new pages in the future (such as a blog page)
Nice to have
• I want a place to store articles I write or use.
• LinkedIn or Twitter Feed
Should not have
• Not fluffy or too 'zen' like personal life coaches tend to present.

```html
<!DOCTYPE html>
<html lang="en">
<head>
<meta charset="utf-8">
<title>Glen Whitmore Professional Coaching</title>
<link href="https://fonts.googleapis.com/css2?family=Roboto:wght@300;400;500;700&display=swap" rel="stylesheet">
<style>
:root{
  --blue:#1e88c9;
  --blue-dark:#0355a3;
  --ink:#1b1b1b;
  --text:#555;
  --muted:#a7a7a7;
  --rule:#e8e8e8;
  --footer:#2d2d2d;
  --footer-bottom:#141414;
  --white:#fff;
}
*{box-sizing:border-box;margin:0;padding:0}
html,body{width:791px;height:1200px;overflow:hidden;background:var(--white)}
body{position:relative;font-family:'Roboto',sans-serif;color:var(--text)}
.abs{position:absolute}
.topline{left:0;top:0;width:791px;height:2px;background:var(--blue)}
.hero{left:0;top:0;width:791px;height:383px;
  background:linear-gradient(180deg,#fff 0%,#eef1f4 12%,#bcc5d1 30%,#98a4b5 50%,#a3aebd 70%,#b9c2ce 100%)}
.brand{left:166px;top:22px;font-size:13px;font-weight:400;color:var(--ink);letter-spacing:.3px;text-transform:uppercase}
.nav{top:15px;left:389px;display:flex;font-size:6.2px;font-weight:500;letter-spacing:.4px;color:#444}
.nav a{text-decoration:none;color:inherit;padding:5px 0;margin-right:18px}
.nav a.active{background:var(--blue);color:var(--white);padding:5px 7px;border-radius:2px;margin-right:10px}
.hero-kicker{left:0;width:791px;top:148px;text-align:center;font-size:25px;font-weight:300;color:var(--white)}
.hero-title{left:0;width:791px;top:176px;text-align:center;font-size:38px;font-weight:700;color:var(--white);text-shadow:0 1px 3px rgba(0,0,0,.25)}
.hero-text{left:240px;width:311px;top:229px;text-align:center;font-size:8px;font-weight:300;line-height:10.5px;color:var(--white)}
.arrow{top:162px;width:28px;height:27px;background:#2f3642;border-radius:2px;display:flex;align-items:center;justify-content:center}
.dots{top:362px;left:374px;display:flex;gap:6px}
.dots span{width:11px;height:2px;background:rgba(255,255,255,.85)}
.dots span.on{background:var(--blue)}
.portrait{left:196px;top:392px;width:170px;height:233px;
  background:linear-gradient(180deg,#f4f4f4 0%,#c9ced8 30%,#6f7f9c 65%,#4a5670 100%)}
.portrait-shadow{left:160px;top:622px;width:260px;height:10px;background:radial-gradient(ellipse,rgba(0,0,0,.12),transparent 70%)}
.h2{font-size:13.5px;font-weight:400;color:var(--ink);display:flex;align-items:center}
.h2::after{content:"";display:inline-block;width:18px;height:1px;background:#888;margin-left:6px;margin-top:4px}
.about-text{left:413px;top:444px;width:212px;font-size:6.2px;line-height:10.4px;color:#333}
.checks{left:413px;top:520px;list-style:none;font-size:6.2px;color:#555}
.checks li{height:16.5px;display:flex;align-items:center}
.checks li::before{content:"";width:5px;height:5px;border-radius:50%;background:var(--blue);margin-right:11px}
.intro{left:167px;top:679px;width:455px;font-size:6.2px;line-height:10.4px;color:#333}
.col{top:727px;width:145px}
.col h3{font-size:7.4px;font-weight:500;letter-spacing:.8px;color:var(--blue);margin-bottom:7px}
.col p{font-size:6.2px;line-height:10.2px;color:#555;letter-spacing:.2px}
.card{top:829px;width:105px}
.card .ph{height:65px}
.card h4{font-size:7.6px;font-weight:500;color:var(--blue);margin:5px 0 3px}
.card p{font-size:6px;line-height:10.4px;color:#666}
.footer{left:0;top:956px;width:791px;height:216px;background:var(--footer)}
.cbox{top:976px;width:146px;height:36px;border:1px solid var(--blue);display:flex}
.cbox .ic{width:34px;background:var(--blue);display:flex;align-items:center;justify-content:center}
.cbox .tx{padding:6px 6px 0 6px;font-size:5.6px;line-height:9px;color:var(--white);font-weight:500}
.cbox .tx small{display:block;color:var(--blue);font-size:4.6px;letter-spacing:.5px;margin-bottom:2px}
.fdivider{left:167px;top:1030px;width:457px;height:1px;background:#444}
.fbrand{left:167px;top:1050px;font-size:10px;color:#bbb;text-transform:uppercase;letter-spacing:.3px}
.ftext{left:167px;top:1078px;width:150px;font-size:6px;line-height:11.5px;color:#999}
.fhead{font-size:7.2px;font-weight:500;color:var(--blue);letter-spacing:.4px}
.fhead::after{content:"";display:block;width:10px;height:1px;background:var(--blue);margin-top:4px}
.flinks{left:323px;top:1071px;list-style:none;font-size:6px;color:#999}
.flinks li{height:11.6px;display:flex;align-items:center}
.flinks li::before{content:"›";margin-right:12px;color:#888}
.social{left:324px;top:1131px;display:flex;gap:3px}
.social span{width:11px;height:12px;border:1px solid #999;border-radius:2px}
.input{left:480px;top:1110px;width:137px;height:20px;border:1px solid #777;border-radius:2px;font-size:6px;color:#999;padding:6px 5px}
.btn{left:480px;top:1135px;width:137px;height:20px;background:var(--blue);border-radius:2px;color:var(--white);font-size:6px;display:flex;align-items:center;justify-content:center}
.bottom{left:0;top:1172px;width:791px;height:28px;background:var(--footer-bottom);color:#999;font-size:6px;display:flex;align-items:center;justify-content:center}
</style>
</head>
<body>
<div class="abs hero" role="img" aria-label="Climber on a snowy mountain summit under a cloudy sky"></div>
<div class="abs topline"></div>
<div class="abs brand">Glen Whitmore</div>
<nav class="abs nav"><a class="active">HOME</a><a>OUR PROCESS</a><a>ABOUT US</a><a>ARTICLES</a><a>CONTACT US</a></nav>
<div class="abs hero-kicker">Best Place For</div>
<div class="abs hero-title">Professional Coaching</div>
<p class="abs hero-text">Lorem ipsum dolor sit amet, consectetur adipiscing elit. Cras eros erat, placerat a eros at, sollicitudin scelerisque ipsum.</p>
<div class="abs arrow" style="left:27px"><svg width="10" height="10" viewBox="0 0 10 10"><path d="M9 5H2M5 1.5L1.5 5 5 8.5" stroke="#fff" stroke-width="2" fill="none"/></svg></div>
<div class="abs arrow" style="left:737px"><svg width="10" height="10" viewBox="0 0 10 10"><path d="M1 5h7M5 1.5L8.5 5 5 8.5" stroke="#fff" stroke-width="2" fill="none"/></svg></div>
<div class="abs dots"><span class="on"></span><span></span><span></span></div>

<div class="abs portrait" role="img" aria-label="Portrait of the coach in a navy blazer"></div>
<div class="abs portrait-shadow"></div>
<h2 class="abs h2" style="left:413px;top:416px">About Us</h2>
<p class="abs about-text">Lorem ipsum dolor sit amet, consectetur adipiscing elit. Cras eros erat, placerat a eros at, sollicitudin scelerisque ipsum. Integer dignissim neque vel elit porttitor sodales. Quisque at sem gravida, gravida libero ut, semper neque. Etiam sed sapien at nibh tincidunt fringilla. Integer fermentum nulla diam. Quisque cursus rutrum dui ut placerat. Sed tempus mi sit amet nibh vestibulum, non vestibulum quam tincidunt.</p>
<ul class="abs checks">
<li>Mauris vel justo a quam sodales tristique ac in nisi.</li>
<li>Praesent molestie nulla et ligula egestas sagittis.</li>
<li>Maecenas vitae libero sed mi eleifend dictum.</li>
<li>Fusce quis diam sed sapien ultricies suscipit.</li>
<li>Morbi eu nulla interdum, aliquam nulla sit amet, consectetur neque.</li>
</ul>

<h2 class="abs h2" style="left:166px;top:652px">Is coaching right for you?</h2>
<p class="abs intro">Lorem ipsum dolor sit amet, consectetur adipiscing elit. Nulla ac magna tristique, bibendum ligula vel, ultrices nibh. In interdum diam arcu, non posuere orci gravida nec. Proin elit dolor, venenatis quis convallis quis, fermentum eu felis. Aenean blandit nisl sit amet risus tempus consequat. Nulla ac elit elit. Mauris commodo lectus ut turpis malesuada convallis. Donec commodo nibh nec eleifend pretium.</p>
<div class="abs col" style="left:166px"><h3>LOREM IPSUM DOLOR SIT</h3><p>Lorem ipsum dolor sit amet, consectetur adipiscing elit. Nulla ac magna tristique, bibendum ligula vel</p></div>
<div class="abs col" style="left:323px"><h3>LOREM IPSUM DOLOR SIT</h3><p>Lorem ipsum dolor sit amet, consectetur adipiscing elit. Nulla ac magna tristique, bibendum ligula vel</p></div>
<div class="abs col" style="left:479px"><h3>LOREM IPSUM DOLOR SIT</h3><p>Lorem ipsum dolor sit amet, consectetur adipiscing elit. Nulla ac magna tristique, bibendum ligula vel</p></div>

<h2 class="abs h2" style="left:166px;top:797px">Our Articles</h2>
<div class="abs card" style="left:167px"><div class="ph" role="img" aria-label="Student reading at a desk" style="background:linear-gradient(135deg,#5a4a3c,#3a4d6e 60%,#d9d4cc)"></div><h4>Phasellus euismod</h4><p>Donec id feugiat nibh. Vestibulum ante ipsum primis in faucibus orci luctus</p></div>
<div class="abs card" style="left:284px"><div class="ph" role="img" aria-label="Hands using a tablet beside a laptop" style="background:linear-gradient(135deg,#e8e4de,#b8b2a8 55%,#6e675e)"></div><h4>Tincidunt interdum</h4><p>Donec id feugiat nibh. Vestibulum ante ipsum primis in faucibus orci luctus</p></div>
<div class="abs card" style="left:401px"><div class="ph" role="img" aria-label="Laptop and notebook on a wooden desk" style="background:linear-gradient(135deg,#8a6a48,#c8c2b8 50%,#9a7a58)"></div><h4>Curabitur condimentum</h4><p>Donec id feugiat nibh. Vestibulum ante ipsum primis in faucibus orci luctus</p></div>
<div class="abs card" style="left:518px"><div class="ph" role="img" aria-label="People writing notes in a workshop" style="background:linear-gradient(135deg,#d8dcd0,#a8b090 50%,#e4dccc)"></div><h4>Faucibus orci luctus</h4><p>Donec id feugiat nibh. Vestibulum ante ipsum primis in faucibus orci luctus</p></div>

<footer class="abs footer"></footer>
<div class="abs cbox" style="left:167px"><div class="ic"><svg width="10" height="13" viewBox="0 0 10 13"><path d="M5 0a4.5 4.5 0 0 0-4.5 4.5C.5 8 5 13 5 13s4.5-5 4.5-8.5A4.5 4.5 0 0 0 5 0zm0 6.3a1.8 1.8 0 1 1 0-3.6 1.8 1.8 0 0 1 0 3.6z" fill="#fff"/></svg></div><div class="tx"><small>VISIT US:</small>Contrary to popular belief,<br>Lorem Ipsum is not simply</div></div>
<div class="abs cbox" style="left:323px"><div class="ic"><svg width="12" height="9" viewBox="0 0 12 9"><rect width="12" height="9" rx="1" fill="#fff"/><path d="M0.5 1l5.5 4 5.5-4" stroke="#1e88c9" fill="none"/></svg></div><div class="tx"><small>MAIL US AT:</small>info@glenwhitmore.com</div></div>
<div class="abs cbox" style="left:478px"><div class="ic"><svg width="11" height="11" viewBox="0 0 11 11"><path d="M2.3 0.5l2 2.2-1 1.3c.6 1.4 1.7 2.6 3.1 3.2l1.3-1 2.2 2-1 1.8C5.3 10 1 5.7 1 1.5z" fill="#fff"/></svg></div><div class="tx"><small>CALL US AT:</small>999-999-9999<br>999-999-9999</div></div>
<div class="abs fdivider"></div>
<div class="abs fbrand">Glen Whitmore</div>
<p class="abs ftext">Lorem ipsum dolor sit amet, consectetur adipiscing elit. Nullam dolor nulla, pulvinar a risus eu, malesuada imperdiet dui. Donec quis elit nec nibh imperdiet porta volutpat ut lacus. Duis viverra mi lacinia nisi eleifend, sed molestie ipsum consectetur.</p>
<div class="abs fhead" style="left:323px;top:1054px">Quick Links</div>
<ul class="abs flinks"><li>Home</li><li>Coaching Process</li><li>About us</li></ul>
<div class="abs fhead" style="left:323px;top:1109px">Follow us on</div>
<div class="abs social"><span></span><span></span><span></span><span></span></div>
<div class="abs fhead" style="left:480px;top:1054px">Subscribe Now</div>
<p class="abs ftext" style="left:480px;top:1071px;width:145px">Lorem ipsum dolor sit amet, consectetur adipiscing elit. Nullam dolor nulla, pulvinar a risus eu, malesuada imperdiet dui.</p>
<div class="abs input">Enter your Email</div>
<div class="abs btn">Subscribe Now</div>
<div class="abs bottom">© glenwhitmore.com All right reserved.</div>
</body>
</html>
```